strength and conditioning business focused on helping people move more efficiently

I need a business card designed for a Philadelphia based company called Brsk Lft Motion (pronounced Brisk Lift). We offer fitness professional services with the idea of helping people feel better and move optimally. We do this by designing and walking through individualized programs as well as minor soft tissue work. Our perfect client would be athletes but we will be marketing to parents who have children that are active They remember their former athletic days and want to get as close as possible back to that feeling. Attached will be the official logo and logo formats. I would love for the design to communicate trustworthy and creative. I would also love for the design to be square with rounded edges.

Target Market(s)

Parents of athletic children
former athletes
athletes

Industry/Entity Type

Fitness

Contact Information for Business Card

Business: Brsk Lft Performance
Name: Coach Calvin Ashworth
Position: Strength and Conditioning Coach / Certified Personal Trainer
Contact: coach.ash@brsklft.com
Text: (555)204-7781

Font styles to use
Serif
Sans Serif

Colors
fbee38
fbee3e
0255a3
3176b5
ffffff

Requirements
Must have
• use of logo
Nice to have
• Square design
rounded edges

```html
<!DOCTYPE html>
<html lang="en">
<head>
<meta charset="utf-8">
<title>Brisk Lift – Business Card</title>
<link href="https://fonts.googleapis.com/css2?family=Montserrat:wght@700&family=Arimo:wght@400&display=swap" rel="stylesheet">
<style>
  :root {
    --navy: #0a2a6c;
    --brand-blue: #0b3a8c;
    --gold: #f2c40f;
    --paper: #f7f7f6;
    --ink: #2a2a2a;
    --backdrop: #d9d9d9;
  }
  html, body {
    margin: 0;
    width: 1200px;
    height: 908px;
    overflow: hidden;
    background: var(--backdrop);
  }
  .stage {
    width: 1200px;
    height: 908px;
    display: flex;
    align-items: center;
    justify-content: center;
    gap: 80px;
  }
  .card {
    width: 440px;
    height: 440px;
    border-radius: 40px;
    box-sizing: border-box;
    position: relative;
  }
  .card--front {
    background: var(--navy);
    display: flex;
    align-items: center;
    justify-content: center;
  }
  .card--back {
    background: var(--paper);
    padding: 100px 38px 0 40px;
  }
  .brand-name {
    margin: 0;
    font-family: "Montserrat", sans-serif;
    font-weight: 700;
    white-space: nowrap;
  }
  .card--front .brand-name {
    color: #ffffff;
    font-size: 50px;
  }
  .card--back .brand-name {
    color: var(--brand-blue);
    font-size: 40px;
  }
  .coach-name {
    margin: 28px 0 0;
    font-family: "Montserrat", sans-serif;
    font-weight: 700;
    font-size: 19px;
    letter-spacing: 2.8px;
    color: var(--brand-blue);
    white-space: nowrap;
  }
  .rule {
    height: 1.5px;
    background: var(--gold);
    margin: 8px 0;
  }
  .coach-title {
    font-family: "Arimo", sans-serif;
    font-size: 13px;
    color: var(--ink);
    margin: 0;
    white-space: nowrap;
  }
  .contacts {
    display: flex;
    gap: 10px;
    font-family: "Arimo", sans-serif;
    font-size: 11.5px;
    color: var(--ink);
    white-space: nowrap;
    margin-top: 10px;
  }
  .contact {
    display: flex;
    align-items: center;
    gap: 4px;
  }
  .contact svg {
    width: 11px;
    height: 11px;
    flex: none;
  }
</style>
</head>
<body>
<main class="stage">
  <section class="card card--front" aria-label="Card front">
    <p class="brand-name">Brisk Lift</p>
  </section>

  <section class="card card--back" aria-label="Card back">
    <p class="brand-name">Brisk Lift</p>
    <p class="coach-name">COACH CALVIN ASHWORTH</p>
    <div class="rule"></div>
    <p class="coach-title">Strength and Conditioning Coach / Certified Personal Trainer</p>
    <div class="rule"></div>
    <div class="contacts">
      <span class="contact">
        <svg viewBox="0 0 12 12" aria-hidden="true"><circle cx="6" cy="6" r="6" fill="#0b3a8c"/><path d="M4 3.2l1 1.3-.6.7c.4.9 1 1.5 1.9 1.9l.7-.6 1.3 1-.5.9c-2.3-.3-4.2-2.2-4.5-4.5z" fill="#fff"/></svg>
        (555)204-7781
      </span>
      <span class="contact">
        <svg viewBox="0 0 12 12" aria-hidden="true"><rect x="0.5" y="2" width="11" height="8" rx="1" fill="#0b3a8c"/><path d="M1 2.6l5 4 5-4" stroke="#fff" stroke-width="1" fill="none"/></svg>
        coach.ash@brsklft.com
      </span>
      <span class="contact">
        <svg viewBox="0 0 12 12" aria-hidden="true"><circle cx="6" cy="6" r="5.5" fill="#0b3a8c"/><path d="M0.8 6h10.4M6 0.5c-2.2 2.8-2.2 8.2 0 11M6 0.5c2.2 2.8 2.2 8.2 0 11" stroke="#fff" stroke-width="0.8" fill="none"/></svg>
        www.brsklft.com
      </span>
    </div>
  </section>
</main>
</body>
</html>
```